Business Card Design

We are looking for a business card designed for our landscaping company. We do landscaping installation & Maintenance Services. We would like to see designs that have basic landscaping in background. We also think it is important to have both of our names and phone numbers on the card. We need something that stands out a little whether it is shape of the card or thickness or design.

Business

Bramblewood Yardworks, bramblewoodyard@mailvista.net, Owen Platt 555-273-9104, Daniel Korbin 555-618-3927

```html
<!DOCTYPE html>
<html lang="en">
<head>
<meta charset="utf-8">
<title>Bramblewood Yardworks — Business Card</title>
<link rel="stylesheet" href="https://fonts.googleapis.com/css2?family=Bodoni+Moda:wght@500;600&family=Open+Sans:wght@400&display=swap">
<style>
  :root {
    --page-bg: #e7e3dd;
    --card-top: #eef1f4;
    --card-mid: #e6e2dc;
    --card-bottom: #ddd3c9;
    --card-edge: rgba(255,255,255,0.8);
    --ink: #1c1c1c;
    --ink-soft: #2a2a2a;
    --foliage: #8a8580;
  }
  html, body {
    margin: 0;
    padding: 0;
    width: 1200px;
    height: 970px;
    overflow: hidden;
    background: var(--page-bg);
  }
  .canvas {
    position: relative;
    width: 1200px;
    height: 970px;
  }
  .card {
    position: absolute;
    left: 65px;
    top: 165px;
    width: 1070px;
    height: 640px;
    border-radius: 26px;
    overflow: hidden;
    background: linear-gradient(180deg, var(--card-top) 0%, var(--card-mid) 55%, var(--card-bottom) 100%);
    box-shadow: 0 0 0 1px var(--card-edge) inset, 0 12px 30px rgba(0,0,0,0.12);
  }
  .card__foliage {
    position: absolute;
    left: 560px;
    top: 270px;
    width: 510px;
    height: 370px;
    background: radial-gradient(ellipse at 65% 75%, rgba(138,133,128,0.55) 0%, rgba(138,133,128,0.25) 45%, rgba(138,133,128,0) 75%);
  }
  .card__company {
    position: absolute;
    left: 0;
    width: 1070px;
    top: 98px;
    margin: 0;
    text-align: center;
    font-family: "Bodoni Moda", serif;
    font-weight: 600;
    font-size: 70px;
    line-height: 1;
    color: var(--ink);
  }
  .card__rule {
    position: absolute;
    left: 110px;
    top: 188px;
    width: 868px;
    height: 2px;
    background: var(--ink);
  }
  .contact {
    position: absolute;
    top: 300px;
  }
  .contact--left { left: 142px; }
  .contact--right { left: 628px; }
  .contact__name {
    margin: 0;
    font-family: "Bodoni Moda", serif;
    font-weight: 500;
    font-size: 46px;
    line-height: 1.1;
    color: var(--ink-soft);
  }
  .contact__phone {
    display: flex;
    align-items: center;
    gap: 12px;
    margin-top: 8px;
    padding-left: 4px;
    font-family: "Open Sans", sans-serif;
    font-size: 34px;
    color: var(--ink-soft);
  }
  .contact__icon { width: 24px; height: 24px; flex: none; }
  .card__email {
    position: absolute;
    left: 0;
    width: 1040px;
    top: 508px;
    text-align: center;
    font-family: "Open Sans", sans-serif;
    font-size: 31px;
    color: var(--ink-soft);
  }
</style>
</head>
<body>
<main class="canvas">
  <section class="card">
    <div class="card__foliage" role="img" aria-label="Soft silhouette of landscaping grasses and fronds"></div>
    <h1 class="card__company">Bramblewood Yardworks</h1>
    <div class="card__rule"></div>

    <div class="contact contact--left">
      <p class="contact__name">Owen Platt</p>
      <div class="contact__phone">
        <svg class="contact__icon" viewBox="0 0 24 24" aria-hidden="true">
          <rect width="24" height="24" fill="#1c1c1c"/>
          <path d="M8 5c1 0 1.6 2.2 1.6 3s-1.3 1-1 2c.6 1.8 1.8 3.2 3.4 4 .9.4 1.2-1 2-1s3 .7 3 1.7c0 1.3-1.4 2.3-2.6 2.3C9.8 17 6 12 6 7.6 6 6.3 7 5 8 5z" fill="#eee"/>
        </svg>
        <span>555-273-9104</span>
      </div>
    </div>

    <div class="contact contact--right">
      <p class="contact__name">Daniel Korbin</p>
      <div class="contact__phone">
        <svg class="contact__icon" viewBox="0 0 24 24" aria-hidden="true">
          <rect width="24" height="24" fill="#1c1c1c"/>
          <path d="M8 5c1 0 1.6 2.2 1.6 3s-1.3 1-1 2c.6 1.8 1.8 3.2 3.4 4 .9.4 1.2-1 2-1s3 .7 3 1.7c0 1.3-1.4 2.3-2.6 2.3C9.8 17 6 12 6 7.6 6 6.3 7 5 8 5z" fill="#eee"/>
        </svg>
        <span>555-618-3927</span>
      </div>
    </div>

    <p class="card__email">bramblewoodyard@mailvista.net</p>
  </section>
</main>
</body>
</html>
```